Personal Training

The name of my company is Heron Motion. I am looking for a design that will feature the 8 components I am utilizing in my workouts (strength, flexibility, agility, core, power, balance, cardiovacular, speed) and represent the spider. It is not essesstial to have a spider for my logo but would be nice. If a spider is used please do not use a logo like Quillboy, a tarantula, or anything scary involving a spider (I have female clients who would get scared) lol
If you need me to provide more information please let me know. Feel free to check my website for ideas but ignore the pictures on my site as those are not pictures of me or clients
Thank you in advance!

Industry/Entity Type

Fitness

Contact Information for Business Card

Glen Marsh
Company Name: Heron Motion
Tag line: Eight paths to a stronger you
Website: hermov7.example
Email: glen@hermov7.example
Cell: 555-314-2268

KERB Certified Personal Trainer
CPR AED National Pulse Society
B.A. Exercise Physiology W.S.T., 2004

```html
<!DOCTYPE html>
<html lang="en">
<head>
<meta charset="utf-8">
<title>Heron Motion — Business Card</title>
<link rel="stylesheet" href="https://fonts.googleapis.com/css2?family=Roboto:wght@500;700&family=Roboto+Condensed:wght@700&display=swap">
<style>
  :root {
    --page: #ecebe8;
    --card-black: #1c1c1d;
    --card-charcoal: #333335;
    --accent-red: #d9494a;
    --accent-red-soft: #e05a5a;
    --text-white: #ffffff;
  }
  html, body {
    margin: 0;
    width: 1200px;
    height: 900px;
    overflow: hidden;
    background: var(--page);
  }
  .card {
    position: absolute;
    left: 100px;
    top: 164px;
    width: 1000px;
    height: 572px;
    background: radial-gradient(circle at 45% 40%, var(--card-charcoal), var(--card-black) 75%);
    overflow: hidden;
    box-shadow: 0 10px 30px rgba(0,0,0,0.25);
    font-family: "Roboto Condensed", "Arial Narrow", sans-serif;
    color: var(--text-white);
  }
  .side-band {
    position: absolute;
    left: 0;
    top: 0;
    width: 240px;
    height: 572px;
  }
  .brand-name {
    position: absolute;
    left: 300px;
    top: 30px;
    margin: 0;
    font-family: "Roboto", Arial, sans-serif;
    font-weight: 700;
    font-size: 76px;
    letter-spacing: -1px;
    color: var(--text-white);
    white-space: nowrap;
  }
  .tagline-ribbon {
    position: absolute;
    left: 240px;
    top: 128px;
    width: 470px;
    height: 40px;
  }
  .tagline {
    position: absolute;
    left: 300px;
    top: 131px;
    margin: 0;
    font-family: "Roboto", Arial, sans-serif;
    font-weight: 500;
    font-size: 25px;
    line-height: 34px;
    color: var(--text-white);
    white-space: nowrap;
  }
  .person {
    position: absolute;
    left: 300px;
    top: 182px;
    width: 270px;
    text-align: right;
  }
  .person-name {
    margin: 0;
    font-family: "Roboto", Arial, sans-serif;
    font-weight: 700;
    font-size: 46px;
    color: var(--accent-red-soft);
    text-align: left;
  }
  .person-role {
    margin: -4px 0 0;
    font-family: "Roboto", Arial, sans-serif;
    font-weight: 700;
    font-size: 20px;
    letter-spacing: 1px;
  }
  .details {
    position: absolute;
    left: 285px;
    top: 278px;
    margin: 0;
    padding: 0;
    list-style: none;
    font-weight: 700;
    font-size: 25px;
    line-height: 35px;
    white-space: nowrap;
  }
  .web-decoration {
    position: absolute;
    right: 0;
    bottom: 0;
    width: 330px;
    height: 330px;
    background: radial-gradient(circle at 100% 100%, rgba(217,73,74,0.55), rgba(217,73,74,0.15) 60%, rgba(217,73,74,0) 72%);
  }
</style>
</head>
<body>
  <article class="card">
    <svg class="side-band" viewBox="0 0 240 572" aria-hidden="true">
      <polygon fill="var(--accent-red)" points="0,0 200,0 200,150 178,170 186,190 168,210 176,240 158,262 166,290 150,310 156,340 138,360 146,390 128,410 134,440 116,460 122,490 104,510 110,572 0,572"/>
      <g fill="none" stroke="var(--text-white)" stroke-width="3">
        <rect x="64" y="168" width="24" height="38" rx="4"/>
        <line x1="72" y1="200" x2="80" y2="200"/>
        <rect x="58" y="232" width="36" height="24"/>
        <polyline points="58,232 76,247 94,232"/>
        <circle cx="76" cy="294" r="16"/>
        <ellipse cx="76" cy="294" rx="7" ry="16"/>
        <line x1="60" y1="294" x2="92" y2="294"/>
      </g>
      <g fill="var(--text-white)">
        <rect class="badge-cert" x="46" y="335" width="60" height="26" rx="13"/>
        <circle class="badge-society" cx="76" cy="396" r="16"/>
        <rect class="badge-school" x="56" y="432" width="40" height="40"/>
      </g>
    </svg>

    <h1 class="brand-name">Heron Motion</h1>
    <svg class="tagline-ribbon" viewBox="0 0 470 40" aria-hidden="true">
      <polygon fill="var(--accent-red-soft)" points="0,0 450,0 470,20 450,40 0,40"/>
    </svg>
    <p class="tagline">Eight paths to a stronger you</p>

    <div class="person">
      <p class="person-name">Glen Marsh</p>
      <p class="person-role">FOUNDER</p>
    </div>

    <ul class="details">
      <li>555-314-2268</li>
      <li>glen@hermov7.example</li>
      <li>www.hermov7.example</li>
      <li>KERB Certified Personal Trainer</li>
      <li>CPR AED National Pulse Society</li>
      <li>B.A. Exercise Physiology W.S.T., 2004</li>
    </ul>

    <div class="web-decoration" role="img" aria-label="Red line-drawn web decoration in the corner"></div>
  </article>
</body>
</html>
```